Lumavento business card

We need a modern business card - With our 4 colors - See web: www.lumavento.dk

I have attached logo and som old business Cards we have - Lets Make the new ones shine...:-) -

Industry/Entity Type

Business

Requirements
Must have
• the logo with lumavento only,

```html
<!DOCTYPE html>
<html lang="da">
<head>
<meta charset="utf-8">
<title>Lumavento visitkort</title>
<link rel="stylesheet" href="https://fonts.googleapis.com/css2?family=Jost:wght@300;400&display=swap">
<style>
  :root {
    --backdrop: #e9e7e3;
    --card-dark: #3f3f40;
    --card-light: #fbfbfb;
    --lime: #7cc653;
    --magenta: #c8318a;
    --orange: #e6843a;
    --purple: #7c3490;
    --ink: #4a4a4a;
  }
  * { margin: 0; padding: 0; box-sizing: border-box; }
  html, body { width: 1200px; height: 1023px; overflow: hidden; }
  body {
    background: var(--backdrop);
    font-family: "Jost", "Futura", sans-serif;
    display: flex;
    flex-direction: column;
    align-items: center;
    justify-content: center;
    gap: 60px;
  }
  .card {
    position: relative;
    width: 640px;
    height: 388px;
    box-shadow: 0 6px 18px rgba(0,0,0,.18);
    overflow: hidden;
  }
  .card--front { background: var(--card-dark); }
  .card--back { background: var(--card-light); }

  .color-tab {
    position: absolute;
    width: 32px;
    height: 86px;
  }
  .color-tab--magenta { right: 0; top: 96px; background: var(--magenta); }
  .color-tab--orange  { right: 0; top: 182px; background: var(--orange); }
  .color-tab--lime    { left: 0; top: 120px; background: var(--lime); }
  .color-tab--purple  { left: 0; top: 206px; background: var(--purple); }

  .brand {
    position: absolute;
    inset: 0;
    display: flex;
    flex-direction: column;
    align-items: center;
    justify-content: center;
    gap: 16px;
  }
  .brand__dot {
    width: 90px;
    height: 90px;
    border: 4px solid var(--lime);
    border-radius: 50%;
  }
  .brand__name {
    color: var(--lime);
    font-weight: 300;
    font-size: 26px;
    letter-spacing: 6px;
  }

  .contact {
    position: absolute;
    left: 70px;
    top: 64px;
    color: var(--ink);
    font-weight: 300;
  }
  .contact__accent {
    width: 40px;
    height: 3px;
    background: var(--lime);
    margin-bottom: 22px;
  }
  .contact__name { font-size: 30px; font-weight: 400; letter-spacing: 1px; }
  .contact__role { font-size: 18px; color: var(--magenta); margin: 4px 0 34px; }
  .contact__line { font-size: 19px; line-height: 1.55; letter-spacing: .5px; }
</style>
</head>
<body>
  <section class="card card--front" aria-label="Forside">
    <span class="color-tab color-tab--magenta"></span>
    <span class="color-tab color-tab--orange"></span>
    <div class="brand">
      <span class="brand__dot"></span>
      <span class="brand__name">lumavento</span>
    </div>
    <span class="color-tab color-tab--lime"></span>
    <span class="color-tab color-tab--purple"></span>
  </section>

  <section class="card card--back" aria-label="Bagside">
    <div class="contact">
      <div class="contact__accent"></div>
      <p class="contact__name">Emil Sander</p>
      <p class="contact__role">Kreativ leder</p>
      <p class="contact__line">Tranevej 14</p>
      <p class="contact__line">2500 Valby</p>
      <p class="contact__line">+45 31 62 40 78</p>
      <p class="contact__line">+45 28 70 36 42</p>
    </div>
  </section>
</body>
</html>
```